Request for Business Card Design

Hi. My name is Marlene, I am looking for a new business card design for my company, Quarrow Signal Instruments, LLC. I really like the design you did for Tarsel Venture and was hoping you could do something similar using our full logo and our mark. I am also open to any raised texture design using our mark. I have attached our full logo, which would need to be somewhere on the card, as well as the mark in both outline and full form, as well as our brand colors / guide. The card does not have to be white, as long as our logo and mark appear. I actually like darker colored business cards more, but am open to all options. If you are interested in working with me, please let me know. We would also take the business card design into letterhead design if you can do that.

```html
<!DOCTYPE html>
<html lang="en">
<head>
<meta charset="utf-8">
<title>Quarrow Signal Instruments – Business Card</title>
<link rel="stylesheet" href="https://fonts.googleapis.com/css2?family=Barlow:wght@600&family=Roboto:wght@400&display=swap">
<style>
  :root {
    --backdrop: #dedede;
    --brand-blue: #0a9ac2;
    --brand-blue-light: #22a6c8;
    --brand-blue-deep: #0b88ab;
    --ink-dark: #3b3b3d;
    --paper: #ffffff;
  }
  html, body {
    margin: 0;
    width: 1200px;
    height: 1200px;
    overflow: hidden;
    background: var(--backdrop);
  }
  .canvas {
    position: relative;
    width: 1200px;
    height: 1200px;
  }
  .card {
    position: absolute;
    top: 303px;
    height: 594px;
    overflow: hidden;
  }
  /* Front card */
  .card-front {
    left: 200px;
    width: 370px;
    background:
      radial-gradient(circle at 30% 25%, var(--brand-blue-light) 0%, transparent 55%),
      linear-gradient(160deg, var(--brand-blue) 0%, var(--brand-blue-deep) 70%, var(--brand-blue) 100%);
  }
  .front-brand {
    position: absolute;
    left: 36px;
    top: 496px;
    display: flex;
    align-items: center;
    gap: 20px;
    color: var(--paper);
    font-family: "Barlow", sans-serif;
    font-weight: 600;
  }
  .brand-dot {
    width: 58px;
    height: 58px;
    border-radius: 50%;
    background: var(--paper);
    flex: none;
  }
  .front-brand .brand-name {
    font-size: 40px;
    letter-spacing: 4px;
    line-height: 1;
  }
  .front-brand .brand-sub {
    font-size: 12.5px;
    letter-spacing: 0.6px;
    margin-top: 4px;
  }
  /* Back card */
  .card-back {
    left: 599px;
    width: 364px;
    background: var(--paper);
  }
  .back-band {
    position: absolute;
    inset: 0;
  }
  .back-brand {
    position: absolute;
    top: 74px;
    left: 0;
    width: 100%;
    text-align: center;
    color: var(--ink-dark);
    font-family: "Barlow", sans-serif;
    font-weight: 600;
  }
  .back-brand .brand-dot {
    width: 60px;
    height: 60px;
    margin: 0 auto 36px;
    background: var(--brand-blue);
  }
  .back-brand .brand-name {
    font-size: 46px;
    letter-spacing: 5px;
    line-height: 1;
  }
  .back-brand .brand-sub {
    font-size: 15px;
    letter-spacing: 0.8px;
    margin-top: 4px;
  }
  .contact-block {
    position: absolute;
    left: 0;
    top: 336px;
    width: 100%;
    text-align: center;
    color: var(--paper);
    font-family: "Roboto", sans-serif;
  }
  .person-name {
    font-size: 27px;
    line-height: 1;
    letter-spacing: 0.3px;
  }
  .person-role {
    font-size: 16px;
    margin-top: 2px;
  }
  .icon-row {
    display: flex;
    align-items: center;
    justify-content: center;
    gap: 4px;
    margin-top: 13px;
  }
  .icon-rule {
    width: 52px;
    height: 1px;
    background: rgba(255,255,255,0.7);
    margin: 0 3px;
  }
  .icon-tile {
    width: 25px;
    height: 25px;
    border-radius: 3px;
    background: var(--paper);
    display: flex;
    align-items: center;
    justify-content: center;
  }
  .contact-lines {
    margin-top: 8px;
    font-size: 16.5px;
    line-height: 21px;
    letter-spacing: 0.3px;
  }
  .contact-divider {
    width: 195px;
    height: 1px;
    background: rgba(255,255,255,0.7);
    margin: 15px auto 13px;
  }
  .address-lines {
    font-size: 16.5px;
    line-height: 21px;
  }
</style>
</head>
<body>
<main class="canvas">
  <section class="card card-front" aria-label="Card front">
    <div class="front-brand">
      <span class="brand-dot"></span>
      <div>
        <div class="brand-name">QUARROW</div>
        <div class="brand-sub">SIGNAL INSTRUMENTS</div>
      </div>
    </div>
  </section>

  <section class="card card-back" aria-label="Card back">
    <svg class="back-band" width="364" height="594" viewBox="0 0 364 594" aria-hidden="true">
      <path d="M0 280 L225 282 Q328 292 364 390 L364 594 L0 594 Z" fill="var(--brand-blue)"/>
    </svg>

    <div class="back-brand">
      <div class="brand-dot"></div>
      <div class="brand-name">QUARROW</div>
      <div class="brand-sub">SIGNAL INSTRUMENTS</div>
    </div>

    <div class="contact-block">
      <div class="person-name">DANIEL VARGA</div>
      <div class="person-role">Managing Director</div>

      <div class="icon-row">
        <span class="icon-rule"></span>
        <span class="icon-tile" aria-label="Phone">
          <svg width="17" height="13" viewBox="0 0 17 13"><path d="M1 5 Q8.5 -1 16 5 L14 6.5 L12 4.5 L12 3.5 Q8.5 2 5 3.5 L5 4.5 L3 6.5 Z M4 7 L13 7 L14 12 L3 12 Z" fill="var(--brand-blue)"/></svg>
        </span>
        <span class="icon-tile" aria-label="Email">
          <svg width="17" height="12" viewBox="0 0 17 12"><rect x="0.5" y="0.5" width="16" height="11" fill="var(--brand-blue)"/><path d="M1 1 L8.5 7 L16 1 M1 11 L6.5 5.5 M16 11 L10.5 5.5" stroke="#fff" stroke-width="1" fill="none"/></svg>
        </span>
        <span class="icon-tile" aria-label="Website">
          <svg width="15" height="15" viewBox="0 0 15 15"><circle cx="7.5" cy="7.5" r="7" fill="var(--brand-blue)"/><path d="M4 3 Q7 2 8 5 Q6 7 4 6 Z M9 8 Q12 8 11 12 Q9 11 9 8 Z" fill="#fff"/></svg>
        </span>
        <span class="icon-rule"></span>
      </div>

      <div class="contact-lines">
        <div>+1 303 555 0147</div>
        <div>info@quarrow.com</div>
        <div>www.quarrow.com</div>
      </div>

      <div class="contact-divider"></div>

      <div class="address-lines">
        <div>2140 Ridgeline Drive, Suite 4</div>
        <div>Boulder, CO 80301, USA</div>
      </div>
    </div>
  </section>
</main>
</body>
</html>
```